Automotive Business Card Design

I would just like a automotive themed card. nothing too extravagant, but catchy.

needs to say something about doing roadside assistance,mobile repairs, Diesel repairs, and Fleet maintenance

it can be single sided or double sided. no preference there.

Industry/Entity Type

Automotive

Contact Information for Business Card

Dean Marlowe
phone 534 861 2093
Name: Brightpath Automotive & Diesel Repair

```html
<!DOCTYPE html>
<html lang="en">
<head>
<meta charset="utf-8">
<title>Brightpath Automotive &amp; Diesel Repair – Business Card</title>
<link rel="stylesheet" href="https://fonts.googleapis.com/css2?family=Cinzel:wght@400;600&family=Open+Sans:wght@400&display=swap">
<style>
  :root {
    --stage: #2b2b2b;
    --card-black: #050505;
    --card-grey: #e3e3e3;
    --ink: #111111;
    --white: #ffffff;
    --gold-light: #f3d98a;
    --gold: #c9a227;
    --gold-deep: #6e5410;
  }
  * { margin: 0; padding: 0; box-sizing: border-box; }
  html, body {
    width: 1200px;
    height: 900px;
    overflow: hidden;
    background: var(--stage);
  }
  .card {
    position: absolute;
    left: 100px;
    top: 164px;
    width: 1000px;
    height: 572px;
    background: var(--card-grey);
    overflow: hidden;
    box-shadow: 0 20px 50px rgba(0,0,0,.5);
  }
  .card__band {
    position: absolute;
    left: 0; top: 0;
    width: 100%;
    height: 318px;
    background: var(--card-black);
  }
  .card__artwork {
    position: absolute;
    left: 0; top: 0;
    width: 100%;
    height: 100%;
  }
  .card__company {
    position: absolute;
    left: 36px;
    top: 34px;
    font-family: "Cinzel", serif;
    font-weight: 600;
    font-size: 31px;
    letter-spacing: 1px;
    color: var(--white);
  }
  .card__name {
    position: absolute;
    left: 40px;
    top: 340px;
    font-family: "Cinzel", serif;
    font-weight: 400;
    font-size: 50px;
    letter-spacing: 1px;
    color: var(--ink);
  }
  .card__phone {
    position: absolute;
    left: 50px;
    top: 440px;
    display: flex;
    align-items: center;
    gap: 34px;
    font-family: "Open Sans", sans-serif;
    font-size: 42px;
    color: var(--ink);
  }
  .card__phone svg { width: 40px; height: 40px; }
  .services {
    position: absolute;
    left: 600px;
    top: 330px;
    font-family: "Open Sans", sans-serif;
    color: var(--ink);
  }
  .services__title {
    font-size: 28px;
    font-weight: 400;
    margin-bottom: 10px;
  }
  .services__list {
    list-style: none;
    margin-left: 110px;
    font-size: 22px;
    line-height: 30px;
  }
  .services__list li {
    position: relative;
    padding-left: 34px;
  }
  .services__list li::before {
    content: "";
    position: absolute;
    left: 0; top: 11px;
    width: 10px; height: 10px;
    border-radius: 50%;
    background: var(--ink);
  }
</style>
</head>
<body>
  <article class="card">
    <div class="card__band">
      <svg class="card__artwork" viewBox="0 0 1000 318" preserveAspectRatio="none" role="img" aria-label="Golden motor oil pouring from a bottle in the top right and splashing across the band">
        <defs>
          <radialGradient id="oilGlow" cx="55%" cy="70%" r="55%">
            <stop offset="0%" stop-color="var(--gold-light)" stop-opacity=".9"/>
            <stop offset="40%" stop-color="var(--gold)" stop-opacity=".7"/>
            <stop offset="75%" stop-color="var(--gold-deep)" stop-opacity=".35"/>
            <stop offset="100%" stop-color="var(--card-black)" stop-opacity="0"/>
          </radialGradient>
          <linearGradient id="bottleTone" x1="0" y1="0" x2="1" y2="0">
            <stop offset="0%" stop-color="#9a9a9a"/>
            <stop offset="100%" stop-color="#e8e8e8"/>
          </linearGradient>
        </defs>
        <rect x="0" y="0" width="1000" height="318" fill="url(#oilGlow)"/>
        <rect x="860" y="0" width="140" height="70" fill="url(#bottleTone)" opacity=".55"/>
      </svg>
      <h1 class="card__company">Brightpath Automotive &amp; Diesel Repair</h1>
    </div>

    <h2 class="card__name">Dean Marlowe</h2>

    <p class="card__phone">
      <svg viewBox="0 0 24 24" aria-hidden="true">
        <path fill="#111" d="M6.6 10.8a15.1 15.1 0 0 0 6.6 6.6l2.2-2.2a1 1 0 0 1 1-.25 11.4 11.4 0 0 0 3.6.57 1 1 0 0 1 1 1V20a1 1 0 0 1-1 1A17 17 0 0 1 3 4a1 1 0 0 1 1-1h3.5a1 1 0 0 1 1 1c0 1.25.2 2.45.57 3.6a1 1 0 0 1-.25 1z"/>
      </svg>
      <span>534 861 2093</span>
    </p>

    <section class="services">
      <h3 class="services__title">Services</h3>
      <ul class="services__list">
        <li>Roadside assistance</li>
        <li>Fleet maintenance</li>
        <li>Diesel repairs</li>
        <li>Mobile repairs</li>
      </ul>
    </section>
  </article>
</body>
</html>
```